URGENT REQUEST Business Card for Executive Coach (already have logo)

Wexford Leadership Consulting is a one person business doing high-end executive coaching, leadership training, and personal transformation work (psychotherapy). I urgently need new cards to fit my new logo.

I would like the card to be scannable by ScanPip and Quillbook Greet.

A draft of the company website is at http://pronve.com/demo/wexford

Target Market(s)

Senior corporate executives

Industry/Entity Type

Leadership

Requirements
Must have

• 1. Please use the company tag line: "The psychology of executive excellence"
2. My name is: Gerald Wexford, PhD (Halbrook)
3. Behind my name, please make "(Halbrook)" in smaller font.
4. My Title: Executive Coach & Leadership Trainer
4. No street address
5. If there is space, please put my current appointments:
Leadership Studies Faculty (KPT)
Supervisor & Coach (OBRAVE)
6. Email: Gwexlen@WexfordConsulting.example
7. Web: www.WexfordConsulting.example
8. Mobile: +65 8476-0000
Nice to have
• Company Tag Line:
• The psychology of executive excellence and personal transformation
• What I provide:
• Executive Coaching
• Leadership Training
• Personal Transformation

```html
<!DOCTYPE html>
<html lang="en">
<head>
<meta charset="utf-8">
<title>Wexford Leadership Consulting – Business Card</title>
<link rel="stylesheet" href="https://fonts.googleapis.com/css2?family=Fira+Sans:wght@700&family=Open+Sans:wght@400;600;700&family=Tinos:ital@1&display=swap">
<style>
  :root {
    --brand-red: #8b181c;
    --paper: #ffffff;
    --edge: #9a9a9a;
    --ink-light: #ffffff;
  }
  * { margin: 0; padding: 0; box-sizing: border-box; }
  html, body {
    width: 1200px;
    height: 686px;
    overflow: hidden;
    background: var(--paper);
  }
  .card {
    position: relative;
    width: 1200px;
    height: 686px;
    background: var(--paper);
    border: 1.5px solid var(--edge);
    border-radius: 46px;
    overflow: hidden;
    font-family: "Open Sans", Arial, sans-serif;
  }
  .brand {
    position: absolute;
    top: 104px;
    left: 0;
    width: 100%;
    text-align: center;
    font-family: "Open Sans", Arial, sans-serif;
    font-weight: 600;
    font-size: 56px;
    letter-spacing: 1px;
    color: var(--brand-red);
  }
  .tagline {
    position: absolute;
    top: 242px;
    left: 0;
    width: 100%;
    text-align: center;
    font-family: "Tinos", "Times New Roman", serif;
    font-style: italic;
    font-size: 39px;
    color: var(--brand-red);
  }
  .band {
    position: absolute;
    top: 343px;
    left: 0;
    width: 100%;
    height: 343px;
    background: var(--brand-red);
    color: var(--ink-light);
  }
  .identity {
    position: absolute;
    right: 303px;
    top: 32px;
    text-align: right;
  }
  .identity__name {
    font-family: "Fira Sans", Arial, sans-serif;
    font-weight: 700;
    font-size: 34px;
    line-height: 44px;
  }
  .identity__school {
    font-size: 26px;
  }
  .identity__title {
    font-size: 22px;
    line-height: 34px;
  }
  .appointments {
    position: absolute;
    left: 48px;
    top: 168px;
    font-size: 22px;
    line-height: 37px;
  }
  .appointments__heading {
    font-weight: 700;
    font-size: 22px;
  }
  .contacts {
    position: absolute;
    right: 91px;
    top: 173px;
    text-align: right;
    font-size: 22px;
    line-height: 35px;
  }
  .contacts__label { font-weight: 700; }
</style>
</head>
<body>
  <div class="card">
    <div class="brand">Wexford Leadership Consulting</div>
    <div class="tagline">The psychology of executive excellence</div>

    <div class="band">
      <div class="identity">
        <div class="identity__name">Gerald Wexford, PhD <span class="identity__school">(Halbrook)</span></div>
        <div class="identity__title">Executive Coach &amp; Leadership Trainer</div>
      </div>

      <div class="appointments">
        <div class="appointments__heading">Current Appointments:</div>
        <div>Supervisor &amp; Coach (OBRAVE)</div>
        <div>Leadership Studies Faculty (KPT)</div>
      </div>

      <div class="contacts">
        <div><span class="contacts__label">M:</span> +65 8476-0000</div>
        <div><span class="contacts__label">W:</span> www.WexfordConsulting.example</div>
        <div><span class="contacts__label">E:</span> Gwexlen@WexfordConsulting.example</div>
      </div>
    </div>
  </div>
</body>
</html>
```